sales brocure for maintenance service company

come up with an eye grabbing sales brochure to highlight our services. we specialize in full facility maintenance we provide janitorial, specialized "cleanroom" cleaning. snow and ice management landscape maintenance, building and facility repair. we only work for commercial, industrial, and educational facilities. you can use some of the photos I uploaded or stock photos our colors are navy blue deep yellow baby/powder blue. I need a design that sells jobs!

```html
<!DOCTYPE html>
<html lang="en">
<head>
<meta charset="utf-8">
<title>Summit Facilities Services – Trifold Brochure</title>
<link href="https://fonts.googleapis.com/css2?family=Roboto+Slab:wght@400;600;700&display=swap" rel="stylesheet">
<style>
  :root{
    --backdrop:#5b4333;
    --paper:#ffffff;
    --paper-shade:#e4e6ea;
    --heading-red:#b3262c;
    --body-ink:#2b2b2b;
    --navy:#24256d;
    --deep-yellow:#f2c21b;
    --band-blue:#1c80c9;
    --tick-red:#c0262c;
  }
  *{box-sizing:border-box;margin:0;padding:0}
  html,body{width:1200px;height:1120px;overflow:hidden;background:var(--backdrop)}
  body{font-family:"Roboto Slab",Georgia,serif;color:var(--body-ink)}
  .brochure{
    position:absolute;left:30px;top:110px;width:1140px;height:900px;
    display:flex;box-shadow:0 18px 40px rgba(0,0,0,.45);
  }
  .panel{
    position:relative;width:380px;height:900px;padding:34px 30px 0;
    background:linear-gradient(180deg,#f7f9fb 0%,var(--paper) 60%);
    border-bottom:14px solid var(--band-blue);
  }
  .panel--inner{background:linear-gradient(90deg,var(--paper-shade) 0%,#ffffff 30%,#ffffff 70%,var(--paper-shade) 100%)}
  .panel--cover{background:linear-gradient(90deg,#eef0f3 0%,#ffffff 40%)}
  h2{font-weight:700;color:var(--heading-red);font-size:19px;line-height:1.2;margin-bottom:6px}
  p{font-size:11.5px;line-height:1.45;margin-bottom:10px}
  .photo{border-radius:10px;margin:14px auto 22px;display:block}
  .checklist{list-style:none;margin:6px 0 16px}
  .checklist li{font-size:11.5px;line-height:1.55;display:flex;align-items:center;gap:8px}
  .checklist svg{flex:none}
  .welcome p{color:var(--heading-red);font-size:14px;line-height:1.45;margin-bottom:14px}
  .brand{position:absolute;left:0;right:0;bottom:70px;text-align:center}
  .brand__row{display:flex;align-items:center;justify-content:center;gap:10px}
  .brand__mark{width:34px;height:34px;border-radius:50%;background:var(--deep-yellow)}
  .brand__name{font-weight:700;color:var(--navy);font-size:34px;letter-spacing:.5px}
  .brand__sub,.brand__place{font-weight:700;color:var(--navy);font-size:15px;letter-spacing:1.5px;text-transform:uppercase}
  .brand__place{color:#333;margin-top:4px}
</style>
</head>
<body>
<main class="brochure">

  <section class="panel panel--intro">
    <h2>About Us</h2>
    <p>Our company is based on the belief that our customers' needs are of the utmost importance. Our entire team is committed to meeting those needs. As a result, a high percentage of our business is from repeat customers and referrals.</p>
    <p>We would welcome the opportunity to earn your trust and deliver you the best service in the industry.</p>
    <p>We offer multiple locations to better serve our customers.</p>
    <h2>Services We Provide</h2>
    <p>We offer a wide range of Landscape, janitorial, and parking lot services to suit a variety of needs and budgets. Our most popular services are shown below. Please call or send an e-mail for more information on services, current promotions and custom options.</p>
    <ul class="checklist">
      <li><svg width="12" height="10" viewBox="0 0 12 10"><path d="M1 5l3 3 7-7" fill="none" stroke="var(--tick-red)" stroke-width="2"/></svg>Janitorial and clean room services</li>
      <li><svg width="12" height="10" viewBox="0 0 12 10"><path d="M1 5l3 3 7-7" fill="none" stroke="var(--tick-red)" stroke-width="2"/></svg>Large area lawn and field mowing</li>
      <li><svg width="12" height="10" viewBox="0 0 12 10"><path d="M1 5l3 3 7-7" fill="none" stroke="var(--tick-red)" stroke-width="2"/></svg>Landscape construction</li>
      <li><svg width="12" height="10" viewBox="0 0 12 10"><path d="M1 5l3 3 7-7" fill="none" stroke="var(--tick-red)" stroke-width="2"/></svg>Hardscape construction</li>
      <li><svg width="12" height="10" viewBox="0 0 12 10"><path d="M1 5l3 3 7-7" fill="none" stroke="var(--tick-red)" stroke-width="2"/></svg>Large and small facility snow management service</li>
    </ul>
    <svg class="photo" width="300" height="150" role="img" aria-label="Photo of a polished commercial hallway with glossy floors"><defs><linearGradient id="hall" x1="0" y1="0" x2="1" y2="1"><stop offset="0" stop-color="#c9b48f"/><stop offset="1" stop-color="#e9e3d6"/></linearGradient></defs><rect width="300" height="150" rx="10" fill="url(#hall)"/></svg>
    <div class="welcome">
      <p>Welcome, and thank you for visiting our site.</p>
      <p>Summit Facility Services Corp is a full service maintenance company providing solutions for daily maintenance needs.</p>
      <p>We specialize in large facility property maintenance, from janitorial needs, clean room services, to Landscaping and irrigation services, snow and ice management, parking lot sweeping, striping, and paving, and trash/recycling removal.</p>
    </div>
  </section>

  <section class="panel panel--inner">
    <h2>Janitorial and Clean Room</h2>
    <p>We offer full service facility cleaning, and we offer clean room services for any type of clean room application.</p>
    <svg class="photo" width="300" height="120" role="img" aria-label="Photo of a gloved hand wiping a clean room surface"><defs><linearGradient id="clean" x1="0" y1="0" x2="1" y2="0"><stop offset="0" stop-color="#3d6fa8"/><stop offset="1" stop-color="#b9d3e8"/></linearGradient></defs><rect width="300" height="120" rx="10" fill="url(#clean)"/></svg>
    <h2>Large Area Lawn &amp; Field Mowing</h2>
    <p>We provide mowing services for large lawn areas of 1-150 acres! also we provide finish mowing for fields, we manage hay production for small horse farms, and provide annual mowing for enviornmentally sensitive areas.</p>
    <svg class="photo" width="300" height="130" role="img" aria-label="Photo of two green riding mowers on a lawn"><defs><linearGradient id="lawn" x1="0" y1="0" x2="0" y2="1"><stop offset="0" stop-color="#5f8a3a"/><stop offset="1" stop-color="#7fae4a"/></linearGradient></defs><rect width="300" height="130" rx="10" fill="url(#lawn)"/></svg>
    <h2>Landscape Construction</h2>
    <p>We provide Landscape construction for new developments, roadsides, and improvements to existing landscapes. we have over 50 pieces of equipment to ensure we can match the right machine for the job with minimal damage to existing lawns and landscape areas. we specialize in large tree plantings and large volume planting jobs.</p>
    <svg class="photo" width="300" height="150" role="img" aria-label="Photo of a landscaped house front with trees and flower beds"><defs><linearGradient id="house" x1="0" y1="0" x2="0" y2="1"><stop offset="0" stop-color="#6f9a4c"/><stop offset=".6" stop-color="#c8bfa8"/><stop offset="1" stop-color="#4f7d36"/></linearGradient></defs><rect width="300" height="150" rx="10" fill="url(#house)"/></svg>
  </section>

  <section class="panel panel--cover">
    <h2>Hard Scape Construction</h2>
    <p>For over 15 years we have been installing brick walkways, patios, pool decks, driveways, walls, and fountains!</p>
    <svg class="photo" width="300" height="110" role="img" aria-label="Photo of a paved stone driveway beside a brick building"><defs><linearGradient id="hard" x1="0" y1="0" x2="1" y2="1"><stop offset="0" stop-color="#6d6a5f"/><stop offset="1" stop-color="#c9b999"/></linearGradient></defs><rect width="300" height="110" rx="10" fill="url(#hard)"/></svg>
    <h2>Large &amp; Small Facility Snow Management Services</h2>
    <p>We offer a wide variety of winter management programs from simple snowplowing to total liability management. we offer multiple contract structures from seasonal, per storm, and per inch options. as well as spring sweeping service included in price.</p>
    <svg class="photo" width="300" height="130" role="img" aria-label="Photo of a yellow loader clearing snow"><defs><linearGradient id="snow" x1="0" y1="0" x2="1" y2="0"><stop offset="0" stop-color="#d9a52a"/><stop offset=".5" stop-color="#e8eef4"/><stop offset="1" stop-color="#9fc3e2"/></linearGradient></defs><rect width="300" height="130" rx="10" fill="url(#snow)"/></svg>
    <div class="brand">
      <div class="brand__row"><span class="brand__mark"></span><span class="brand__name">Summit</span></div>
      <div class="brand__sub">Facilities Services</div>
      <div class="brand__place">Harlow, MA</div>
    </div>
  </section>

</main>
</body>
</html>
```